Card design for orthopaedic surgeons working as The Brightwater Joint Centre

Business cards, letterhead

Colors

Designer to choose colors to be used in the design.

Requirements
Must have
• Late addition.
• Cards letterhead must have logos of
• Crestmoor Lindell College of Surgeons
• Varenwood Bone Health Association
Nice to have
• Back of card to have space for appointment time to be added by hand and some blank space for writing incidental other notes.

```html
<!DOCTYPE html>
<html lang="en">
<head>
<meta charset="utf-8">
<title>The Brightwater Joint Centre – Business Cards</title>
<link href="https://fonts.googleapis.com/css2?family=Poppins:wght@300;400;500;600&display=swap" rel="stylesheet">
<style>
  :root {
    --navy: #05304b;
    --sky: #2aa4ee;
    --white: #ffffff;
    --badge: #3d6683;
    --backdrop: #8a8a8a;
    --backdrop-dark: #6f6f6f;
  }
  * { margin: 0; padding: 0; box-sizing: border-box; }
  html, body { width: 1200px; height: 960px; overflow: hidden; }
  body {
    background: linear-gradient(135deg, var(--backdrop) 0%, var(--backdrop-dark) 100%);
    font-family: "Poppins", sans-serif;
    position: relative;
  }
  .card {
    position: absolute;
    width: 560px;
    height: 320px;
    border-radius: 22px;
    overflow: hidden;
    box-shadow: 0 14px 30px rgba(0,0,0,0.35);
  }
  /* Back of card */
  .card-back {
    left: 80px; top: 130px;
    background: var(--navy);
    color: var(--white);
    display: flex; flex-direction: column; align-items: center; justify-content: center;
  }
  .brand-name {
    font-weight: 300;
    font-size: 30px;
    letter-spacing: -0.5px;
    white-space: nowrap;
  }
  .card-back .brand-name { color: var(--white); }
  .website-row {
    margin-top: 10px;
    display: flex; align-items: center; gap: 12px;
  }
  .website-rule { width: 40px; height: 1px; background: var(--white); }
  .website { font-size: 13px; font-weight: 300; letter-spacing: 3px; }
  .affiliations {
    position: absolute; bottom: 22px; left: 0; right: 0;
    display: flex; justify-content: center; gap: 18px;
  }
  .affiliation-badge {
    width: 30px; height: 30px; border-radius: 50%;
    background: var(--badge);
  }
  /* Front of card */
  .card-front {
    left: 560px; top: 510px;
    background: var(--white);
  }
  .wave { position: absolute; inset: 0; }
  .card-front .brand-name {
    position: absolute; right: 40px; top: 62px;
    font-size: 26px; color: var(--sky);
  }
  .holder {
    position: absolute; left: 132px; bottom: 24px; color: var(--white);
  }
  .holder-name { font-size: 22px; font-weight: 600; line-height: 1.15; white-space: nowrap; }
  .holder-title { font-size: 14px; font-weight: 500; margin-bottom: 6px; }
  .holder-address { font-size: 13px; font-weight: 300; line-height: 1.35; white-space: nowrap; }
  .contacts {
    position: absolute; right: 30px; top: 196px;
    list-style: none; color: var(--white);
    font-size: 13px; font-weight: 300; line-height: 1.55;
  }
  .contacts li { display: flex; align-items: center; gap: 8px; }
  .contacts svg { width: 12px; height: 12px; fill: var(--white); flex: none; }
</style>
</head>
<body>

<section class="card card-back" aria-label="Business card back">
  <div class="brand-name">The Brightwater Joint Centre</div>
  <div class="website-row">
    <span class="website-rule"></span>
    <span class="website">www.brightwaterjointcentre.com</span>
    <span class="website-rule"></span>
  </div>
  <div class="affiliations">
    <span class="affiliation-badge" role="img" aria-label="Crestmoor Lindell College of Surgeons badge"></span>
    <span class="affiliation-badge" role="img" aria-label="Varenwood Bone Health Association badge"></span>
  </div>
</section>

<section class="card card-front" aria-label="Business card front">
  <svg class="wave" viewBox="0 0 560 320" preserveAspectRatio="none" aria-hidden="true">
    <path d="M18 320 C44 232 100 186 240 172 C400 156 520 140 560 44 L560 320 Z" fill="var(--sky)"/>
    <path d="M30 320 C56 240 112 196 248 182 C408 166 526 150 560 62 L560 320 Z" fill="var(--navy)"/>
    <path d="M44 320 C70 254 116 214 212 194 C140 220 86 260 56 320 Z" fill="var(--sky)"/>
  </svg>

  <div class="brand-name">The Brightwater Joint Centre</div>

  <div class="holder">
    <div class="holder-name">Daniel Hartley</div>
    <div class="holder-title">President</div>
    <div class="holder-address">2140 Harbor View Road<br>Millbrook, Oregon 97410</div>
  </div>

  <ul class="contacts">
    <li><svg viewBox="0 0 24 24"><path d="M6.6 10.8a15.1 15.1 0 0 0 6.6 6.6l2.2-2.2c.3-.3.7-.4 1-.2 1.1.4 2.3.6 3.6.6.6 0 1 .4 1 1V20c0 .6-.4 1-1 1A17 17 0 0 1 3 4c0-.6.4-1 1-1h3.5c.6 0 1 .4 1 1 0 1.3.2 2.5.6 3.6.1.3 0 .7-.2 1z"/></svg>555-204-7731</li>
    <li><svg viewBox="0 0 24 24"><path d="M7 1h10a2 2 0 0 1 2 2v18a2 2 0 0 1-2 2H7a2 2 0 0 1-2-2V3a2 2 0 0 1 2-2zm0 3v14h10V4z"/></svg>555-318-4096</li>
    <li><svg viewBox="0 0 24 24"><path d="M6 2h12v6H6zM3 9h18v10h-3v3H6v-3H3zm5 6v5h8v-5z"/></svg>555-462-1185</li>
    <li><svg viewBox="0 0 24 24"><path d="M2 5h20v14H2zm2 2v.5l8 5 8-5V7z"/></svg>info@brightwaterjc.com</li>
  </ul>
</section>

</body>
</html>
```